Design of a promotional offer flyer required to promote low-cost websites to 1-man band businesses

I want a flyer designed - either a double-sided A5 flyer or even A4 folded into a third double-sided. The flyer is to showcase a new service - low-cost websites for 1-man-band businesses, business startups and tradesmen in England. Look at the copy, find some pix and let me know! Flyer will be printed and used as an image on my website too. Pix could be related to some of the target groups. We need to stress the simple message that websites start from £5 per week and this is an-all-in-one fee.

Target Market(s)

Tradesmen, business start ups and 1-man band businesses that want a website

Industry/Entity Type

Small Business

Contact Information for Business Card

All contact details and name of business to be confirmed shortly

Font styles to use
Serif

Requirements
Must have
• Basic messages from copy for flyer i.e. websites from £5 per week and what each client gets for that price to be included on the business card! Please read copy for the flyer.
Nice to have
• Nice background image or series of small images relevant to the target audience. Again, see list of targets from copy for flyer.
Should not have
• I don't want exact or similar design to my main business Blue Harbour Promotions. The new flyer and business card should be a different and distinct branding to that of Blue Harbour Promotions. Aimed at a more economical style, whilst looking professional, but relevant to the target audiences.

```html
<!DOCTYPE html>
<html lang="en">
<head>
<meta charset="utf-8">
<title>Low-Cost Websites Folded Flyer</title>
<link href="https://fonts.googleapis.com/css2?family=Archivo+Black&family=Oswald:wght@500;700&family=Open+Sans:ital,wght@0,400;0,600;0,700;0,800;1,400&display=swap" rel="stylesheet">
<style>
:root{
  --red:#e0141b;
  --red-dark:#b30d12;
  --black:#141414;
  --charcoal:#2a2a2a;
  --yellow:#ffe400;
  --white:#ffffff;
  --paper:#f4f4f4;
  --stage:#e3e3e3;
  --text:#1d1d1d;
  --photo-warm:#d9b9a3;
  --photo-blue:#1f4f78;
}
*{margin:0;padding:0;box-sizing:border-box}
html,body{width:848px;height:1200px;overflow:hidden;background:var(--stage)}
body{position:relative;font-family:'Open Sans',Arial,sans-serif;color:var(--text)}
.spread{position:absolute;left:30px;width:788px;height:540px;display:flex;box-shadow:0 6px 18px rgba(0,0,0,.18)}
.spread--outside{top:30px}
.spread--inside{top:630px}
.panel{position:relative;width:394px;height:540px;background:var(--white);overflow:hidden}
.panel+.panel{border-left:1px solid #dcdcdc}
.abs{position:absolute}
.photo{position:absolute}

/* back cover */
.back .crowd{left:0;top:0;width:394px;height:280px;background:linear-gradient(180deg,#fbfbfb 0%,#e4e4e4 55%,#f2f2f2 100%)}
.offer-heading{font-family:'Oswald',sans-serif;font-weight:700;font-style:italic;font-size:17px;text-align:center;width:100%;top:108px}
.offer-box{left:70px;top:138px;width:254px;border:1px solid #555;border-radius:7px;background:var(--white);padding:7px 10px;text-align:center;font-size:10px;font-style:italic;line-height:1.45}
.offer-box .cost{color:var(--red);font-weight:700;font-style:italic;font-size:11px}
.back .red-band{left:0;top:300px;width:394px;height:170px;background:var(--red)}
.price-tile{left:18px;top:285px;width:170px;height:170px;background:var(--black);color:var(--white);font-family:'Oswald',sans-serif;font-style:italic;font-weight:700;text-align:center;padding-top:10px;line-height:1.05}
.price-tile .big{display:block;color:var(--yellow);font-size:54px}
.price-tile .line{display:block;font-size:17px;text-transform:uppercase}
.price-tile .hl{color:var(--yellow)}
.back-contact{left:205px;top:318px;width:180px;color:var(--white);font-size:10px;font-style:italic;line-height:1.55}
.call-yellow{left:205px;top:410px;color:var(--yellow);font-family:'Oswald',sans-serif;font-size:19px;font-weight:500}
.back .web-strip{left:190px;top:445px;width:204px;height:30px;background:var(--white);font-size:12px;font-weight:600;padding:7px 0 0 22px}
.black-foot{left:0;bottom:0;width:394px;height:44px;background:var(--black)}

/* front cover */
.front .hero{left:40px;top:0;width:354px;height:245px;background:radial-gradient(ellipse at 65% 45%,var(--photo-warm) 0%,#9fb8cc 45%,#ffffff 80%)}
.headline{left:20px;top:250px;width:360px;text-align:center;font-family:'Archivo Black',sans-serif;line-height:1.05}
.headline .h1{display:block;color:var(--red);font-size:31px}
.headline .h2{display:block;color:var(--charcoal);font-size:19px}
.front .red-band{left:0;top:322px;width:394px;height:92px;background:var(--red);color:var(--white);text-align:center;font-weight:800;font-size:14px;line-height:1.3;padding:10px 16px 0}
.front .red-band .yellow{color:var(--yellow);font-size:15px}
.front .dark-band{left:0;top:414px;width:394px;height:64px;background:var(--black);color:var(--white);font-size:9.2px;text-align:center;line-height:1.45;padding:6px 14px 0}

/* inside left */
.inside-top{left:0;top:0;width:394px;height:14px;background:linear-gradient(90deg,var(--black) 0 70%,var(--red) 70%)}
.inside-left .model{left:200px;top:22px;width:180px;height:130px;background:linear-gradient(160deg,#6b5a50 0%,var(--photo-warm) 45%,#f2f2f2 100%)}
.list-title{left:22px;top:70px;font-family:'Archivo Black',sans-serif;font-size:19px;line-height:1.1}
.benefits{left:22px;top:150px;width:355px;font-size:10.6px;line-height:1.35;list-style:none}
.benefits li{position:relative;padding-left:14px;margin-bottom:3px}
.benefits li::before{content:"";position:absolute;left:0;top:5px;width:6px;height:6px;border-radius:50%;background:var(--red)}
.benefits .short{max-width:190px}
.inside-left .red-foot{left:0;bottom:0;width:394px;height:66px;background:var(--red);color:var(--white);font-family:'Archivo Black',sans-serif;font-size:17px;padding:22px 0 0 40px}
.inside-left .red-foot .sep{margin:0 12px;font-family:'Open Sans',sans-serif;font-weight:400}
.inside-left .black-strip{left:0;bottom:66px;width:394px;height:10px;background:var(--black)}

/* inside right */
.inside-right .top-red{left:0;top:0;width:394px;height:14px;background:var(--red)}
.inside-right .globe{left:0;top:14px;width:394px;height:130px;background:radial-gradient(ellipse at 45% 60%,#c8d9e8 0%,#4b85b3 35%,var(--photo-blue) 65%,#0c2238 100%)}
.fee-text{left:30px;top:160px;width:334px;text-align:center;font-family:'Oswald',sans-serif;font-weight:500;font-size:17px;line-height:1.2}
.promo{left:22px;top:240px;width:350px;border:1.5px solid var(--black);padding:10px 12px;text-align:center}
.promo .title{font-family:'Oswald',sans-serif;font-weight:500;color:var(--red);font-size:25px;line-height:1.1}
.promo .body{font-weight:700;font-size:12px;line-height:1.4;margin-top:4px}
.promo .cost{font-family:'Archivo Black',sans-serif;color:var(--red);font-size:19px;margin-top:4px}
.inside-right .red-foot{left:0;bottom:0;width:394px;height:66px;background:var(--red);color:var(--white);font-family:'Archivo Black',sans-serif;font-size:20px;padding:20px 0 0 30px}
.inside-right .man{left:236px;top:360px;width:158px;height:180px;background:linear-gradient(180deg,#e6c8b3 0%,#cfdced 55%,#b9c9dd 100%)}
.inside-right .black-strip{left:0;bottom:66px;width:236px;height:10px;background:var(--black)}
</style>
</head>
<body>

<section class="spread spread--outside">
  <article class="panel back">
    <div class="photo crowd" role="img" aria-label="Faint greyscale silhouettes of business people walking through a city"></div>
    <h3 class="abs offer-heading">Promotional Offer :</h3>
    <div class="abs offer-box">
      Order your new 5-page website before ............<br>
      and we'll set up a Chatterbox Page for FREE.<br>
      <span class="cost">Normal Cost: £97 plus VAT!</span>
    </div>
    <div class="abs red-band"></div>
    <div class="abs price-tile">
      <span class="big">£5</span>
      <span class="line">Per week for a</span>
      <span class="line">1-page website or</span>
      <span class="line hl">£10 per week</span>
    </div>
    <p class="abs back-contact">
      Email: TBC<br>
      For further information or to order.<br>
      Full terms and conditions at www. TBC.<br>
      All fees plus VAT.
    </p>
    <p class="abs call-yellow">CALL : TBC</p>
    <div class="abs web-strip">www.&nbsp; TBC</div>
    <div class="abs black-foot"></div>
  </article>

  <article class="panel front">
    <div class="photo hero" role="img" aria-label="Smiling young woman pointing at a laptop showing app icons and a tablet"></div>
    <h1 class="abs headline">
      <span class="h1">WANT A WEBSITE -</span>
      <span class="h2">WITHOUT IT COSTING THE EARTH?</span>
    </h1>
    <div class="abs red-band">
      Professionally-designed websites for tradesmen, business start-ups and 1-man bands from only<br>
      <span class="yellow">£5 per week and NO upfront costs!</span>
    </div>
    <p class="abs dark-band">
      Suitable for plumbers, electricians, roofers, builders, painters and decorators, joiners, business start-ups, 1-man bands such as hairdressers, photographers, fitness instructors, window cleaners, beauticians, gardeners, odd job men, wheelie bin cleaners, IFAs or self-employed consultants.
    </p>
    <div class="abs black-foot"></div>
  </article>
</section>

<section class="spread spread--inside">
  <article class="panel inside-left">
    <div class="abs inside-top"></div>
    <div class="photo model" role="img" aria-label="Young woman presenting an open laptop showing a website"></div>
    <h2 class="abs list-title">Here's<br>what you get :</h2>
    <ul class="abs benefits">
      <li class="short">Professionally-designed 1-page or 5-page website (Home, About Us, Services, Contact Us, News)</li>
      <li>Responsive design that displays properly on mobiles and tablets</li>
      <li>On-going changes and updates</li>
      <li>All text written for you</li>
      <li>Photographs (Royalty-free stock images)</li>
      <li>Professional email addresses e.g. info@yourcompany.co.uk, sales@yourcompany.co.uk and yourname@yourcompany.co.uk. We'll even set up these email addresses on your PC and laptop!</li>
      <li>Links to your social media accounts</li>
      <li>Up to 2 hours' changes each month to content, pix, and adding new pages</li>
      <li>Professional hosting for your website and email</li>
      <li>No upfront cost! Just weekly, monthly or annual invoice - you choose!</li>
    </ul>
    <div class="abs black-strip"></div>
    <div class="abs red-foot">Email: TBC<span class="sep">|</span>Visit www. TBC</div>
  </article>

  <article class="panel inside-right">
    <div class="abs top-red"></div>
    <div class="photo globe" role="img" aria-label="Hand touching a glowing globe linked by a network of people icons"></div>
    <p class="abs fee-text">For an-all-in fee from only £5 per week for a 1-page website or £10 per week for a 5-page website.</p>
    <div class="abs promo">
      <p class="title">Promotional Offer :</p>
      <p class="body">order your new 5-page website before ............<br>and we'll set up a Chatterbox Page for FREE.</p>
      <p class="cost">Normal Cost: £97 plus VAT!</p>
    </div>
    <div class="abs black-strip"></div>
    <div class="abs red-foot">Call:&nbsp; TBC</div>
    <div class="photo man" role="img" aria-label="Smiling businessman in shirt and red tie giving a thumbs up"></div>
  </article>
</section>

</body>
</html>
```